TL - business card

Tallow Partners is an insurance brokerage firm, inovative, proactive, vigorous, which aims to become the leader of the insurance brokers in Anfrica. We should like to get some designs which should be avoided also in Gray / Metallic for the Administration and Orange / Blue for the Managers (ike in the picture sent). The Blue / Green logo is not the correct one, but the source of the file. Please adjust the color accordingly for the business cards. 1 / Orange / Blue 2 / Gray / Metallic We want something classic but which is transmitted strenght, inovation, modernity and most of all, rapidity. We want something start-up like, very punchy and catching eye remaining profesional at the same time. Name: Dorian Whitlock Function: Managing Director Address: N ° 17/18 Rua Veloso - R / C 2B Direita - Bairro Mutamba - Luanda Tel: (+244) 947 582 316 Email: dorian.whitlock@tallow-p.example Website: www.tallow-p. example We want classic in the front and creative, colorfull at the back. The cards will be printed in relief, with very high quality of paper.
Insurance Broker
Colors
Designer to choose colors to be used in the design.

```html
<!DOCTYPE html>
<html lang="en">
<head>
<meta charset="utf-8">
<title>Tallow Partners – Business Card</title>
<link href="https://fonts.googleapis.com/css2?family=Montserrat:wght@400;500;700&display=swap" rel="stylesheet">
<style>
  :root {
    --backdrop: #161616;
    --card: #1f1f1f;
    --card-edge: #262626;
    --metal: #b9b9b9;
    --accent: #1fa3e0;
    --ink: #f2f2f2;
    --muted: #d8d8d8;
  }
  * { margin: 0; padding: 0; box-sizing: border-box; }
  html, body {
    width: 1200px; height: 900px; overflow: hidden;
    background: var(--backdrop);
    font-family: "Montserrat", sans-serif;
  }
  .sheet {
    width: 1200px; height: 900px;
    display: flex; flex-direction: column;
    align-items: center; justify-content: center; gap: 40px;
  }
  .card {
    width: 700px; height: 400px;
    background: linear-gradient(160deg, var(--card-edge), var(--card));
    position: relative;
  }
  /* front */
  .card-front {
    display: flex; align-items: center; justify-content: center; gap: 18px;
  }
  .brand-dot {
    width: 46px; height: 46px; border-radius: 50%;
    background: var(--metal);
  }
  .brand-name {
    font-weight: 700; font-size: 38px; letter-spacing: 1px;
    color: var(--metal); text-transform: uppercase;
  }
  /* back */
  .card-back {
    display: flex; align-items: center; justify-content: center;
  }
  .identity {
    text-align: right; padding-right: 30px;
  }
  .person-name {
    font-weight: 500; font-size: 32px; letter-spacing: 2px;
    color: var(--accent); text-transform: uppercase; line-height: 1.1;
  }
  .person-role {
    font-size: 17px; color: var(--ink); margin-top: 4px; letter-spacing: .5px;
  }
  .divider {
    width: 2px; height: 130px; background: var(--accent);
  }
  .contact {
    padding-left: 32px; color: var(--muted);
    font-size: 17px; line-height: 1.45; letter-spacing: .4px;
  }
  .contact-address { margin-bottom: 6px; }
  .contact-line { display: flex; align-items: center; gap: 10px; }
  .contact-line svg { width: 14px; height: 14px; flex: none; }
</style>
</head>
<body>
<main class="sheet">
  <section class="card card-front" aria-label="Card front">
    <span class="brand-dot"></span>
    <span class="brand-name">Tallow Partners</span>
  </section>

  <section class="card card-back" aria-label="Card back">
    <div class="identity">
      <h1 class="person-name">Dorian Whitlock</h1>
      <p class="person-role">Managing Director</p>
    </div>
    <div class="divider"></div>
    <div class="contact">
      <p class="contact-address">N ° 17/18 Rua Veloso<br>R / C 2B Direita<br>Bairro Mutamba - Luanda</p>
      <p class="contact-line">
        <svg viewBox="0 0 24 24" aria-hidden="true"><path fill="var(--accent)" d="M6.6 10.8a15.1 15.1 0 0 0 6.6 6.6l2.2-2.2c.3-.3.7-.4 1-.2 1.1.4 2.3.6 3.6.6.6 0 1 .4 1 1V20c0 .6-.4 1-1 1A17 17 0 0 1 3 4c0-.6.4-1 1-1h3.5c.6 0 1 .4 1 1 0 1.3.2 2.5.6 3.6.1.3 0 .7-.2 1z"/></svg>
        +244 947 582 316
      </p>
      <p class="contact-line">
        <svg viewBox="0 0 24 24" aria-hidden="true"><rect x="2.5" y="5" width="19" height="14" fill="none" stroke="var(--accent)" stroke-width="2"/><path d="M3 6l9 7 9-7" fill="none" stroke="var(--accent)" stroke-width="2"/></svg>
        dorian.whitlock@tallow-p.example
      </p>
    </div>
  </section>
</main>
</body>
</html>
```